Boutique custom software development company needs new business card

Our nearly 20 year old custom software development company would like to better include the fact that we are now providing Bitcoin services. These new services are B2B include education (how to acquire and securely hold Bitcoin) and integrating Bitcoin payments into existing ecommerce sites or other existing systems. Please keep the card clean and simple. Attached is our current design and some other files. vextorial.com

Target Market(s)

businesses owners interested in long term relationship

Industry/Entity Type

Custom software development and Bitcoin

Contact Information for Business Card

Dale Parker, dale@vextorial.com, vextorial.com, (888) 555-VXTRL

Font styles to use
Other font styles liked:
• monospace

Requirements
Must have
• double-sided
Nice to have
• clean and simple
Should not have
• physical address

```html
<!DOCTYPE html>
<html lang="en">
<head>
<meta charset="utf-8">
<title>Vextorial Business Card</title>
<link rel="stylesheet" href="https://fonts.googleapis.com/css2?family=Montserrat:wght@300;400;500;800&family=Oswald:wght@600&display=swap">
<style>
  :root {
    --stage: #2b2b2c;
    --card: #1c1d1f;
    --orange: #f47b20;
    --blue: #3f72c4;
    --ink: #f2f2f2;
    --divider: #3a3b3e;
  }
  * { box-sizing: border-box; margin: 0; padding: 0; }
  html, body { width: 1200px; height: 689px; overflow: hidden; }
  body {
    background: var(--stage);
    font-family: "Montserrat", sans-serif;
    position: relative;
  }
  .card {
    position: absolute;
    top: 190px;
    width: 540px;
    height: 309px;
    background: var(--card);
    border-radius: 22px;
    overflow: hidden;
    box-shadow: 0 18px 40px rgba(0,0,0,0.45);
  }
  .card--back { left: 40px; }
  .card--front { left: 620px; }

  .brand { position: absolute; }
  .brand__name {
    display: block;
    font-weight: 800;
    color: var(--blue);
    letter-spacing: 1px;
    line-height: 1;
  }
  .brand__tagline {
    display: block;
    font-weight: 400;
    color: var(--blue);
    line-height: 1;
    margin-top: 6px;
  }
  .card--back .brand { left: 0; right: 0; top: 118px; text-align: center; }
  .card--back .brand__name { font-size: 52px; }
  .card--back .brand__tagline { font-size: 19px; }

  .card--front .brand { left: 36px; top: 120px; }
  .card--front .brand__name { font-size: 36px; }
  .card--front .brand__tagline { font-size: 13.5px; }

  .divider {
    position: absolute;
    left: 290px;
    top: 62px;
    width: 1px;
    height: 130px;
    background: var(--divider);
  }
  .contact { position: absolute; left: 316px; top: 66px; }
  .contact__name {
    font-family: "Oswald", sans-serif;
    font-weight: 600;
    font-size: 27px;
    color: var(--orange);
    text-transform: uppercase;
    letter-spacing: 0.5px;
    line-height: 1;
    margin-bottom: 14px;
  }
  .contact__list { list-style: none; }
  .contact__item {
    display: flex;
    align-items: center;
    gap: 9px;
    color: var(--ink);
    font-size: 14px;
    font-weight: 500;
    line-height: 1;
    margin-bottom: 10px;
  }
  .contact__icon { width: 14px; height: 14px; flex: none; }

  .stripe { position: absolute; left: 0; right: 0; }
  .stripe--orange { bottom: 26px; height: 5px; background: var(--orange); }
  .stripe--blue { bottom: 0; height: 19px; background: var(--blue); }
  .stripe-dot {
    position: absolute;
    right: 62px;
    bottom: 6px;
    width: 46px;
    height: 46px;
    border-radius: 50%;
    background: var(--orange);
    border: 4px solid var(--card);
  }
</style>
</head>
<body>

  <section class="card card--back" aria-label="Card back">
    <div class="brand">
      <span class="brand__name">VEXTORIAL</span>
      <span class="brand__tagline">developer of custom applications</span>
    </div>
  </section>

  <section class="card card--front" aria-label="Card front">
    <div class="brand">
      <span class="brand__name">VEXTORIAL</span>
      <span class="brand__tagline">developer of custom applications</span>
    </div>

    <div class="divider"></div>

    <div class="contact">
      <p class="contact__name">Dale Parker</p>
      <ul class="contact__list">
        <li class="contact__item">
          <svg class="contact__icon" viewBox="0 0 24 24" aria-hidden="true"><path fill="var(--blue)" d="M6.6 10.8a15.1 15.1 0 0 0 6.6 6.6l2.2-2.2a1 1 0 0 1 1-.25 11.4 11.4 0 0 0 3.6.57 1 1 0 0 1 1 1V20a1 1 0 0 1-1 1A17 17 0 0 1 3 4a1 1 0 0 1 1-1h3.5a1 1 0 0 1 1 1c0 1.25.2 2.45.57 3.57a1 1 0 0 1-.25 1z"/></svg>
          (888) 555-VXTRL
        </li>
        <li class="contact__item">
          <svg class="contact__icon" viewBox="0 0 24 24" aria-hidden="true"><rect x="2" y="5" width="20" height="14" rx="1.5" fill="var(--blue)"/><path d="M3 6l9 7 9-7" fill="none" stroke="var(--card)" stroke-width="1.8"/></svg>
          dale@vextorial.com
        </li>
        <li class="contact__item">
          <svg class="contact__icon" viewBox="0 0 24 24" aria-hidden="true"><g fill="none" stroke="var(--blue)" stroke-width="2"><circle cx="12" cy="12" r="9.5"/><ellipse cx="12" cy="12" rx="4" ry="9.5"/><path d="M2.5 12h19M4 7h16M4 17h16"/></g></svg>
          vextorial.com
        </li>
      </ul>
    </div>

    <div class="stripe stripe--orange"></div>
    <div class="stripe stripe--blue"></div>
    <div class="stripe-dot"></div>
  </section>

</body>
</html>
```